Lawn Sign For Construction Projects - Brisk Harbor

This contest is for a lawn sign that will be placed in the front yard of recently completed construction projects. The goal here is to have a bold advertising sign that is visible from a vehicle driving past.

We are still deciding on the default size for our sign, we also may use multiple sizes. The two sizes we will more than likely be using are: 18"h x 24"w and 24"h x 36"w.

Preference will be given to designers that submit original designs that tie into our current brand and are either in both the size formats listed above or are easy to scale in photoshop or illustrator.

In the files, you will see our logo and an example of a lawn sign.

Please contact us with any questions or comments you may have!

Thank You,
- The Brisk Harbor Team
Updates

Project Deadline Extended Reason: We Currently to not have any designs worth choosing. Added Monday, March 21, 2016

Industry/Entity Type

Residential Construction

Colors
34a7d8
ffffff
faa54b

Requirements
Nice to have
• 1. The sign must tie into our current branding and color scheme.
• 2. The sign must be clearly visible and readable.
• 3. The sign must include our phone number in readable print.
• 4. Our website written in small print along the bottom of the sign.
• 5. Must mention we install the following products:
• a.) Solar
• b.) Roofing
• c.) Windows
• d.) Artificial Lawn
• e.) Whole House Fans
• f.) Patio Covers

```html
<!DOCTYPE html>
<html lang="en">
<head>
<meta charset="utf-8">
<title>Brisk Harbor – Lawn Sign</title>
<link rel="stylesheet" href="https://fonts.googleapis.com/css2?family=Open+Sans:wght@300;400;600;700&display=swap">
<style>
  :root {
    --orange: #faa54b;
    --blue: #34a7d8;
    --cream: #fefad9;
    --brand-orange: #f07f2c;
    --white: #ffffff;
  }
  * { margin: 0; padding: 0; box-sizing: border-box; }
  html, body { width: 1200px; height: 900px; overflow: hidden; }
  body { font-family: "Open Sans", Arial, sans-serif; background: var(--orange); }

  .sign { position: relative; width: 1200px; height: 900px; background: var(--orange); overflow: hidden; }

  .header-shapes { position: absolute; left: 0; top: 0; width: 1200px; height: 240px; }

  .brand { position: absolute; left: 0; top: 0; width: 370px; height: 240px;
    display: flex; flex-direction: column; align-items: center; justify-content: center; gap: 14px; }
  .brand-dot { width: 56px; height: 56px; border-radius: 50%; background: var(--brand-orange); }
  .brand-name { font-weight: 700; font-size: 42px; letter-spacing: -0.5px; color: var(--brand-orange); line-height: 1; white-space: nowrap; }

  .phone { position: absolute; left: 620px; top: 82px; font-weight: 600; font-size: 60px;
    color: var(--white); line-height: 1; letter-spacing: 0.5px; }

  .services-title { position: absolute; left: 212px; top: 340px; font-weight: 300; font-size: 76px;
    line-height: 90px; color: var(--white); letter-spacing: 1px; }

  .services-list { position: absolute; left: 214px; top: 540px; width: 900px;
    display: grid; grid-template-columns: 360px 500px; row-gap: 26px; list-style: none; }
  .service { display: flex; align-items: center; height: 56px; color: var(--white);
    font-size: 34px; font-weight: 400; }
  .service-arrow { width: 44px; height: 16px; margin-right: 28px; flex: none; }

  .footer-band { position: absolute; left: 0; top: 846px; width: 1200px; height: 42px; background: var(--blue);
    display: flex; align-items: center; justify-content: flex-end; padding-right: 26px; }
  .website { color: var(--white); font-size: 27px; font-weight: 400; line-height: 1; }
</style>
</head>
<body>
<div class="sign">
  <svg class="header-shapes" viewBox="0 0 1200 240" aria-hidden="true">
    <rect x="0" y="0" width="560" height="240" fill="var(--cream)"/>
    <path d="M350 0 C360 130 410 240 530 240 H1200 V0 Z" fill="var(--blue)"/>
  </svg>

  <div class="brand">
    <span class="brand-dot"></span>
    <span class="brand-name">BRISK HARBOR</span>
  </div>

  <div class="phone">0800-555-0192</div>

  <h1 class="services-title">OUR<br>SERVICES</h1>

  <ul class="services-list">
    <li class="service"><svg class="service-arrow" viewBox="0 0 44 16"><path d="M0 8 H42 M34 2 L42 8 L34 14" fill="none" stroke="#fff" stroke-width="2"/></svg>Solar</li>
    <li class="service"><svg class="service-arrow" viewBox="0 0 44 16"><path d="M0 8 H42 M34 2 L42 8 L34 14" fill="none" stroke="#fff" stroke-width="2"/></svg>Artificial Lawn</li>
    <li class="service"><svg class="service-arrow" viewBox="0 0 44 16"><path d="M0 8 H42 M34 2 L42 8 L34 14" fill="none" stroke="#fff" stroke-width="2"/></svg>Roofing</li>
    <li class="service"><svg class="service-arrow" viewBox="0 0 44 16"><path d="M0 8 H42 M34 2 L42 8 L34 14" fill="none" stroke="#fff" stroke-width="2"/></svg>Whole House Fans</li>
    <li class="service"><svg class="service-arrow" viewBox="0 0 44 16"><path d="M0 8 H42 M34 2 L42 8 L34 14" fill="none" stroke="#fff" stroke-width="2"/></svg>Windows</li>
    <li class="service"><svg class="service-arrow" viewBox="0 0 44 16"><path d="M0 8 H42 M34 2 L42 8 L34 14" fill="none" stroke="#fff" stroke-width="2"/></svg>Patio Covers</li>
  </ul>

  <div class="footer-band"><span class="website">www.briskharbor.com</span></div>
</div>
</body>
</html>
```